Whitcombe Business Card Design

The name of the business is Dario Whitcombe, CPA LLC
The service that we offer is Accounting, Tax & Consulting Services. I need it to have the following items:
Dario Whitcombe, Principal
Phone Number
Email Address
Physical Address

I have attached the company logo, one in black and one in white. Please provide a design in black background and the other in white background. Please include "Accounting, Tax & Consulting Services". I want the business card to be clean and very professional.

```html
<!DOCTYPE html>
<html lang="en">
<head>
<meta charset="utf-8">
<title>Dario Whitcombe, CPA LLC — Business Cards</title>
<link href="https://fonts.googleapis.com/css2?family=Montserrat:wght@400;500;600;700&family=Mulish:wght@400;500&display=swap" rel="stylesheet">
<style>
  :root {
    --stage: #1c1c1c;
    --card-dark: #222223;
    --card-light: #ffffff;
    --brand-red: #9b1c20;
    --mark-grey: #4a4a4c;
    --text-grey: #6d6d70;
    --text-light: #f2f2f2;
  }
  * { box-sizing: border-box; margin: 0; padding: 0; }
  html, body { width: 1200px; height: 927px; overflow: hidden; }
  body { background: var(--stage); position: relative; font-family: "Mulish", sans-serif; }

  .card {
    position: absolute;
    width: 640px;
    height: 366px;
    border-radius: 28px;
    overflow: hidden;
    box-shadow: 0 14px 34px rgba(0,0,0,.55);
  }

  /* Back card: dark brand face */
  .card--back { left: 90px; top: 80px; background: var(--card-dark); }
  .back__lockup {
    position: absolute; left: 96px; top: 118px;
    display: flex; align-items: center; gap: 22px;
  }
  .brand-square { width: 62px; height: 62px; background: var(--brand-red); flex: none; }
  .back__text { display: flex; flex-direction: column; gap: 8px; }
  .brand-name {
    font-family: "Montserrat", sans-serif; font-weight: 500;
    font-size: 27px; letter-spacing: .5px; color: var(--mark-grey);
    text-transform: uppercase;
  }
  .brand-title {
    font-family: "Montserrat", sans-serif; font-weight: 600;
    font-size: 21px; letter-spacing: 3px; color: var(--text-grey);
    text-transform: uppercase;
  }
  .brand-services {
    font-family: "Montserrat", sans-serif; font-weight: 700;
    font-size: 15px; color: var(--mark-grey); margin-top: 6px;
  }

  /* Front card: white brand panel + dark contact panel */
  .card--front { left: 470px; top: 480px; background: var(--card-dark); }
  .front__brand {
    position: absolute; left: 0; top: 0; width: 300px; height: 100%;
    background: var(--card-light);
    display: flex; flex-direction: column; align-items: center; justify-content: center; gap: 10px;
  }
  .front__brand .brand-square { width: 40px; height: 40px; margin-bottom: 6px; }
  .front__brand .brand-name { font-size: 17px; color: var(--mark-grey); letter-spacing: .3px; }
  .front__brand .brand-title { font-size: 11px; letter-spacing: 2px; color: #8a8a8d; font-weight: 500; }

  .name-band {
    position: absolute; left: 300px; top: 58px; right: 0; height: 46px;
    background: var(--brand-red);
    display: flex; align-items: center; padding-left: 22px;
    font-family: "Montserrat", sans-serif; font-weight: 700;
    font-size: 17px; color: var(--text-light); text-transform: uppercase;
  }
  .contact-list {
    position: absolute; left: 322px; top: 140px; right: 20px;
    list-style: none; display: flex; flex-direction: column; gap: 14px;
  }
  .contact-item {
    display: flex; align-items: flex-start; gap: 12px;
    font-size: 14px; line-height: 1.35; color: var(--text-light);
  }
  .contact-icon {
    width: 22px; height: 22px; border-radius: 50%; background: var(--brand-red);
    flex: none; display: flex; align-items: center; justify-content: center;
  }
  .contact-icon svg { width: 12px; height: 12px; fill: none; stroke: var(--text-light); stroke-width: 2; stroke-linecap: round; stroke-linejoin: round; }
</style>
</head>
<body>

  <section class="card card--back" aria-label="Business card back">
    <div class="back__lockup">
      <span class="brand-square"></span>
      <div class="back__text">
        <span class="brand-name">Dario Whitcombe, CPA LLC</span>
        <span class="brand-title">Certified Public Accountant</span>
        <span class="brand-services">Accounting, Tax &amp; Consulting Services</span>
      </div>
    </div>
  </section>

  <section class="card card--front" aria-label="Business card front">
    <div class="front__brand">
      <span class="brand-square"></span>
      <span class="brand-name">Dario Whitcombe, CPA LLC</span>
      <span class="brand-title">Certified Public Accountant</span>
    </div>

    <div class="name-band">Dario Whitcombe, Principal</div>

    <ul class="contact-list">
      <li class="contact-item">
        <span class="contact-icon"><svg viewBox="0 0 24 24"><path d="M12 22s7-7 7-12a7 7 0 0 0-14 0c0 5 7 12 7 12z"/><circle cx="12" cy="10" r="2.5"/></svg></span>
        <span>#208-C, Harlow Court Plaza,<br>Fenwick Road, Brookdale, 402117</span>
      </li>
      <li class="contact-item">
        <span class="contact-icon"><svg viewBox="0 0 24 24"><path d="M5 3h4l2 5-2.5 1.5a11 11 0 0 0 6 6L16 13l5 2v4a2 2 0 0 1-2 2A16 16 0 0 1 3 5a2 2 0 0 1 2-2z"/></svg></span>
        <span>555-204-7391</span>
      </li>
      <li class="contact-item">
        <span class="contact-icon"><svg viewBox="0 0 24 24"><rect x="3" y="5" width="18" height="14" rx="1"/><path d="M3 6l9 7 9-7"/></svg></span>
        <span>info@dariowhitcombecpa.com</span>
      </li>
      <li class="contact-item">
        <span class="contact-icon"><svg viewBox="0 0 24 24"><circle cx="12" cy="12" r="9"/><path d="M3 12h18M12 3a14 14 0 0 1 0 18M12 3a14 14 0 0 0 0 18"/></svg></span>
        <span>www.dariowhitcombecpa.com</span>
      </li>
    </ul>
  </section>

</body>
</html>
```